TALMORK

The business want a professional looking business card. We have a scetch we will add but want the extra upgrade, and would like more suggestions for variations of our business cards.

```html
<!DOCTYPE html>
<html lang="en">
<head>
<meta charset="UTF-8">
<title>TALMORK Business Card</title>
<link href="https://fonts.googleapis.com/css2?family=Playfair+Display:wght@700;900&family=Montserrat:wght@400;500&display=swap" rel="stylesheet">
<style>
  :root {
    --backdrop: #4b4b4b;
    --card: #141414;
    --gold: #d4a93a;
    --gold-light: #f3d77a;
    --gold-dark: #9c7420;
    --white: #f2f2f2;
    --silver: #8a8a8a;
  }
  html, body {
    margin: 0;
    padding: 0;
    width: 1200px;
    height: 800px;
    overflow: hidden;
    background: var(--backdrop);
  }
  .canvas {
    position: relative;
    width: 1200px;
    height: 800px;
    background: radial-gradient(ellipse at 40% 30%, #565656 0%, var(--backdrop) 55%, #3c3c3c 100%);
  }
  .card {
    position: absolute;
    background: var(--card);
    border-radius: 26px;
    border: 3px solid var(--gold);
    box-shadow: 0 24px 40px rgba(0,0,0,0.45);
    box-sizing: border-box;
  }
  .card--front {
    left: 150px;
    top: 100px;
    width: 350px;
    height: 600px;
    padding: 60px 36px 40px;
    display: flex;
    flex-direction: column;
  }
  .card--back {
    left: 560px;
    top: 235px;
    width: 560px;
    height: 330px;
    display: flex;
    align-items: center;
    justify-content: center;
  }
  .brand {
    display: flex;
    flex-direction: column;
    align-items: center;
  }
  .brand__dot {
    width: 64px;
    height: 64px;
    border-radius: 50%;
    background: var(--gold);
    margin-bottom: 34px;
  }
  .brand__name {
    font-family: "Playfair Display", serif;
    font-weight: 700;
    font-size: 46px;
    letter-spacing: 3px;
    color: var(--gold);
    line-height: 1;
  }
  .brand__since {
    font-family: "Montserrat", sans-serif;
    font-weight: 500;
    font-size: 11px;
    letter-spacing: 9px;
    color: var(--gold);
    margin-top: 10px;
    padding-left: 9px;
  }
  .person {
    margin-top: 70px;
  }
  .person__name {
    font-family: "Playfair Display", serif;
    font-weight: 900;
    font-size: 27px;
    line-height: 1.1;
    background: linear-gradient(180deg, var(--gold-light) 0%, var(--gold) 50%, var(--gold-dark) 100%);
    -webkit-background-clip: text;
    background-clip: text;
    color: transparent;
  }
  .person__role {
    font-family: "Montserrat", sans-serif;
    font-size: 15px;
    color: var(--white);
    margin-top: 8px;
  }
  .contacts {
    list-style: none;
    margin: 28px 0 0;
    padding: 0;
    font-family: "Montserrat", sans-serif;
    font-size: 14px;
    color: var(--white);
  }
  .contacts li {
    display: flex;
    align-items: center;
    gap: 10px;
    margin-bottom: 9px;
  }
  .contacts svg {
    width: 14px;
    height: 14px;
    fill: var(--gold);
    flex: none;
  }
  .back-mark {
    display: flex;
    align-items: center;
    gap: 18px;
  }
  .back-mark__dot {
    width: 54px;
    height: 54px;
    border-radius: 50%;
    background: var(--silver);
  }
  .back-mark__name {
    font-family: "Playfair Display", serif;
    font-weight: 700;
    font-size: 44px;
    letter-spacing: 3px;
    color: var(--silver);
  }
</style>
</head>
<body>
<div class="canvas">
  <section class="card card--front">
    <div class="brand">
      <div class="brand__dot"></div>
      <div class="brand__name">TALMORK</div>
      <div class="brand__since">SINCE 2026</div>
    </div>
    <div class="person">
      <div class="person__name">Erik Lunde Haugsrud</div>
      <div class="person__role">CEO &amp; Founder</div>
    </div>
    <ul class="contacts">
      <li>
        <svg viewBox="0 0 24 24" aria-hidden="true"><path d="M6.6 10.8a15.1 15.1 0 0 0 6.6 6.6l2.2-2.2a1 1 0 0 1 1-.25 11.4 11.4 0 0 0 3.6.57 1 1 0 0 1 1 1V20a1 1 0 0 1-1 1A17 17 0 0 1 3 4a1 1 0 0 1 1-1h3.5a1 1 0 0 1 1 1c0 1.25.2 2.45.57 3.57a1 1 0 0 1-.25 1z"/></svg>
        004791234567
      </li>
      <li>
        <svg viewBox="0 0 24 24" aria-hidden="true"><path d="M2 5h20v14H2z M2 5l10 8 10-8" fill="none" stroke="#d4a93a" stroke-width="2.4"/></svg>
        talmork.llc@mailbox.com
      </li>
      <li>
        <svg viewBox="0 0 24 24" aria-hidden="true"><circle cx="12" cy="12" r="9" fill="none" stroke="#d4a93a" stroke-width="2.2"/><path d="M3 12h18M12 3c3 3 3 15 0 18M12 3c-3 3-3 15 0 18" fill="none" stroke="#d4a93a" stroke-width="1.8"/></svg>
        www.talmork.llc
      </li>
    </ul>
  </section>

  <section class="card card--back">
    <div class="back-mark">
      <div class="back-mark__dot"></div>
      <div class="back-mark__name">TALMORK</div>
    </div>
  </section>
</div>
</body>
</html>
```